Boutique Technology Consultancy specialising is Electronic and physical security

We need to redo our existing outdated website. For your reference the link www.pelu.com.au

```html
<!DOCTYPE html>
<html lang="en">
<head>
<meta charset="utf-8">
<title>Pelu Services</title>
<link href="https://fonts.googleapis.com/css2?family=Lato:wght@400;700&display=swap" rel="stylesheet">
<style>
:root{
  --red:#d32a26;
  --ink:#111;
  --grey:#777;
  --field:#e6e6e6;
  --blush:#f8e6e5;
  --deco:#e4e4e4;
  --black:#000;
  --white:#fff;
}
*{box-sizing:border-box;margin:0;padding:0}
html,body{width:1200px;height:4110px;overflow:hidden}
body{position:relative;font-family:'Lato',sans-serif;color:var(--ink);background:var(--white)}
.abs{position:absolute}
.brand{display:flex;align-items:center;gap:10px;font-weight:700;color:var(--ink)}
.brand-mark{background:var(--red)}
.brand-name{line-height:1}
.brand-name small{display:block;letter-spacing:.5em;font-size:.3em;margin-top:4px}
.header{left:0;top:0;width:1200px;height:82px;background:var(--white)}
.nav{font-size:15px}
.nav a{color:inherit;text-decoration:none;position:absolute;white-space:nowrap}
.social{display:flex}
.social span{display:flex;align-items:center;justify-content:center;border-radius:50%;border:1.5px solid currentColor}
.social svg{fill:none;stroke:currentColor;stroke-width:2;stroke-linecap:round;stroke-linejoin:round}
.hero{left:0;top:82px;width:1200px;height:587px;background:linear-gradient(100deg,#3a3f5e 0%,#5b5f86 45%,#8a7a8c 70%,#3c3860 100%)}
.hero-title{left:98px;top:298px;color:var(--white);font-weight:700;font-size:34px;line-height:39px}
.btn{display:flex;align-items:center;justify-content:center;background:var(--red);color:var(--white);border-radius:10px}
.section-title{width:1200px;left:0;text-align:center;font-weight:700;font-size:44px}
.rule{height:4px;width:82px;background:var(--red)}
.lead{text-align:center;color:var(--grey);font-size:16px;line-height:28px}
.card{background:var(--white);border-radius:14px;box-shadow:0 0 14px rgba(0,0,0,.14)}
.card-img{left:12px;top:13px;width:418px;height:235px;border-radius:14px;background:linear-gradient(160deg,#bbb,#444)}
.card h3{position:absolute;left:22px;top:278px;font-size:26px;font-weight:700;color:#222}
.card p{position:absolute;left:24px;top:325px;width:400px;font-size:21px;line-height:29px;color:var(--grey)}
.arrow{width:22px;height:22px;border-radius:50%;display:flex;align-items:center;justify-content:center}
.tile{border-radius:12px;color:var(--white);font-size:17px;text-align:center;display:flex;align-items:flex-end;justify-content:center;padding:0 12px 14px;line-height:21px}
.body-text{font-size:21px;line-height:30px}
.list{list-style:none;font-size:16px;color:#444}
.list li{position:relative;padding-left:22px;height:26px}
.list li::before{content:"›";position:absolute;left:0;top:-3px;color:var(--red);font-size:20px}
.small-text{font-size:16px;line-height:26px;color:#444}
.field{background:var(--field);border-radius:8px;font-size:15px;color:#333;padding:16px 17px}
.pins{list-style:none;font-size:17px;color:#333}
.pins li{height:34px;display:flex;align-items:center;gap:16px}
.footer{left:0;top:3648px;width:1200px;height:462px;background:var(--black);color:var(--white)}
</style>
</head>
<body>

<header class="abs header">
  <div class="abs brand" style="left:96px;top:18px">
    <span class="brand-mark" style="width:40px;height:40px"></span>
    <span class="brand-name" style="font-size:38px">PELU<small>SERVICES</small></span>
  </div>
  <nav class="nav" style="color:#222">
    <a style="left:342px;top:32px">Welcome</a>
    <a style="left:454px;top:32px">Experience</a>
    <a style="left:577px;top:32px">Services</a>
    <a style="left:681px;top:32px">Team</a>
    <a style="left:766px;top:32px">About</a>
    <a style="left:857px;top:32px">Contact</a>
  </nav>
  <div class="abs social" style="left:953px;top:29px;gap:5px;color:var(--red)">
    <span style="width:25px;height:25px"><svg width="13" height="13" viewBox="0 0 24 24"><rect x="3" y="5" width="18" height="14" rx="2"/><path d="M3 7l9 6 9-6"/></svg></span>
    <span style="width:25px;height:25px"><svg width="13" height="13" viewBox="0 0 24 24"><path d="M5 3h4l2 5-3 2a11 11 0 0 0 6 6l2-3 5 2v4a2 2 0 0 1-2 2A17 17 0 0 1 3 5a2 2 0 0 1 2-2z"/></svg></span>
    <span style="width:25px;height:25px"><svg width="13" height="13" viewBox="0 0 24 24"><circle cx="12" cy="12" r="9"/><path d="M3 12h18M12 3a14 14 0 0 1 0 18M12 3a14 14 0 0 0 0 18"/></svg></span>
    <span style="width:25px;height:25px"><svg width="13" height="13" viewBox="0 0 24 24"><path d="M12 21s-7-6-7-11a7 7 0 0 1 14 0c0 5-7 11-7 11z"/><circle cx="12" cy="10" r="2.5"/></svg></span>
    <span style="width:25px;height:25px"><svg width="13" height="13" viewBox="0 0 24 24"><path d="M4 5h16v11H9l-5 4z"/></svg></span>
  </div>
</header>

<section class="abs hero" role="img" aria-label="Smiling professional woman working at a laptop in a blue-lit technology office">
  <div class="abs brand" style="left:98px;top:130px;color:var(--white)">
    <span class="brand-mark" style="width:70px;height:70px"></span>
    <span class="brand-name" style="font-size:96px">PELU<small>SERVICES</small></span>
  </div>
  <h1 class="abs hero-title">YOUR TECHNOLOGY PROJECTS<br>MADE EASY.</h1>
  <a class="abs btn" style="left:98px;top:400px;width:204px;height:58px;font-size:25px">Get Started</a>
</section>

<section id="experience">
  <h2 class="abs section-title" style="top:748px">EXPERIENCE</h2>
  <div class="abs rule" style="left:559px;top:814px"></div>
  <p class="abs lead" style="left:190px;width:820px;top:840px">PELU has a diverse range of project experience across a range of industries within both the public and private sectors. The following is a small sample of some of the clients and sites we have worked with.</p>

  <div class="abs arrow" style="left:90px;top:1166px;background:#999"><svg width="12" height="12" viewBox="0 0 12 12"><path d="M8 2 4 6l4 4" stroke="#fff" stroke-width="2" fill="none"/></svg></div>
  <div class="abs arrow" style="left:1081px;top:1166px;background:#111"><svg width="12" height="12" viewBox="0 0 12 12"><path d="M4 2l4 4-4 4" stroke="#fff" stroke-width="2" fill="none"/></svg></div>

  <article class="abs card" style="left:140px;top:924px;width:444px;height:480px">
    <div class="abs card-img" role="img" aria-label="Black and white photo of a brick tower beneath a glass cone roof"></div>
    <h3>Harbour Central</h3>
    <p>Security technology design consulting for this popular retail and entertainment hub which is managed by the Northline Group.</p>
  </article>
  <article class="abs card" style="left:616px;top:924px;width:444px;height:480px">
    <div class="abs card-img" role="img" aria-label="Black and white photo of cars passing under a motorway toll gantry"></div>
    <h3>CoastLink</h3>
    <p>Virtual servers, network and CCTV upgrade design and project management for this landmark road transportation Public Private Partnership (PPP).</p>
  </article>
</section>

<section id="services">
  <div class="abs" style="left:0;top:1602px;width:721px;height:470px;background:var(--blush);border-radius:0 0 220px 0"></div>
  <div class="abs tile" style="left:99px;top:1527px;width:246px;height:289px;background:linear-gradient(180deg,#6a6560,#2b2b2f)" role="img" aria-label="Team discussing plans in a warehouse">Strategy</div>
  <div class="abs tile" style="left:378px;top:1583px;width:246px;height:289px;background:linear-gradient(180deg,#9aa29a,#2e3238)" role="img" aria-label="Colleagues planning at a table with sticky notes">Projects</div>
  <div class="abs tile" style="left:99px;top:1843px;width:246px;height:288px;background:linear-gradient(180deg,#8a8e94,#24303f)" role="img" aria-label="Technicians working on an electrical cabinet">Operations and<br>Maintenance</div>
  <div class="abs tile" style="left:378px;top:1898px;width:246px;height:288px;background:linear-gradient(180deg,#7c8590,#1f2630)" role="img" aria-label="Two colleagues reviewing a laptop">PELU's services cover a<br>broad range of<br>technologies including</div>

  <h2 class="abs" style="left:678px;top:1688px;font-size:44px;font-weight:700">SERVICES</h2>
  <div class="abs rule" style="left:680px;top:1756px;width:74px"></div>
  <p class="abs body-text" style="left:678px;top:1788px;width:440px">PELU Services provides independent professional services for projects as well as operations and maintenance. We offer end to end services including:</p>
</section>

<section id="about">
  <h2 class="abs section-title" style="top:2322px">ABOUT</h2>
  <div class="abs rule" style="left:559px;top:2388px"></div>
  <p class="abs lead" style="left:195px;width:810px;top:2413px">PELU Services was established in 2016 by Tom Harlow to provide technology consulting services to corporate and government clients with a focus on</p>
  <ul class="abs list" style="left:150px;top:2515px">
    <li>Property/facilities management</li>
    <li>Asset management</li>
    <li>Development and Construction</li>
  </ul>
  <p class="abs small-text" style="left:174px;top:2604px;width:410px">In 2022, PELU Services merged KDS Group into its operations, bringing increased capacity and capability to the NSW office.</p>
  <p class="abs small-text" style="left:174px;top:2698px;width:432px">PELU is a privately owned independent consultancy 100% dedicated to customer satisfaction. With experience in a range of technologies such as internet of things, security systems, wi-fi, building services</p>
  <a class="abs btn" style="left:175px;top:2824px;width:159px;height:46px;font-size:19px;border-radius:9px">Read More</a>
  <div class="abs" style="left:905px;top:2700px;width:230px;height:230px;border:34px solid var(--deco);transform:rotate(18deg)"></div>
  <div class="abs" style="left:650px;top:2492px;width:400px;height:395px;border-radius:0 0 200px 0;background:linear-gradient(150deg,#2b4f7a,#5c86b3 55%,#1d3656)" role="img" aria-label="Two engineers reviewing a tablet in a control room"></div>
</section>

<section id="contact">
  <div class="abs" style="left:482px;top:3103px;width:718px;height:437px;background:var(--blush);border-radius:0 0 0 140px"></div>
  <div class="abs field" style="left:99px;top:3147px;width:241px;height:49px">First Name</div>
  <div class="abs field" style="left:356px;top:3147px;width:241px;height:49px">Last Name</div>
  <div class="abs field" style="left:99px;top:3211px;width:498px;height:49px">Email</div>
  <div class="abs field" style="left:99px;top:3277px;width:498px;height:49px">Subject</div>
  <div class="abs field" style="left:99px;top:3339px;width:498px;height:137px">Message</div>
  <a class="abs btn" style="left:102px;top:3495px;width:159px;height:47px;font-size:19px;border-radius:9px">Send Now</a>

  <h2 class="abs" style="left:664px;top:3162px;font-size:44px;font-weight:700">CONTACT US</h2>
  <div class="abs rule" style="left:665px;top:3228px;width:74px"></div>
  <p class="abs body-text" style="left:664px;top:3263px;width:390px">PELU acknowledges the traditional custodians of the land where our offices are located</p>
  <ul class="abs pins" style="left:664px;top:3379px">
    <li><svg width="10" height="14" viewBox="0 0 10 14"><path d="M5 0a5 5 0 0 0-5 5c0 4 5 9 5 9s5-5 5-9a5 5 0 0 0-5-5z" fill="#d32a26"/><circle cx="5" cy="5" r="2" fill="#f8e6e5"/></svg>Melbourne - Wurundjeri People of the Kulin Nation</li>
    <li><svg width="10" height="14" viewBox="0 0 10 14"><path d="M5 0a5 5 0 0 0-5 5c0 4 5 9 5 9s5-5 5-9a5 5 0 0 0-5-5z" fill="#d32a26"/><circle cx="5" cy="5" r="2" fill="#f8e6e5"/></svg>Sydney - Gadigal People of the Eora Nation</li>
    <li><svg width="10" height="14" viewBox="0 0 10 14"><path d="M5 0a5 5 0 0 0-5 5c0 4 5 9 5 9s5-5 5-9a5 5 0 0 0-5-5z" fill="#d32a26"/><circle cx="5" cy="5" r="2" fill="#f8e6e5"/></svg>Brisbane - Turrbal and Jagera/Yuggera Peoples</li>
  </ul>
</section>

<footer class="abs footer">
  <div class="abs brand" style="left:388px;top:60px;color:var(--white)">
    <span class="brand-mark" style="width:90px;height:90px"></span>
    <span class="brand-name" style="font-size:100px">PELU<small>SERVICES</small></span>
  </div>
  <nav class="nav" style="color:var(--white);font-size:17px">
    <a style="left:284px;top:244px">Welcome</a>
    <a style="left:408px;top:244px">Experience</a>
    <a style="left:544px;top:244px">Services</a>
    <a style="left:660px;top:244px">Team</a>
    <a style="left:756px;top:244px">About</a>
    <a style="left:856px;top:244px">Contact</a>
  </nav>
  <div class="abs social" style="left:485px;top:302px;gap:8px;color:var(--white)">
    <span style="width:40px;height:40px"><svg width="20" height="20" viewBox="0 0 24 24"><rect x="3" y="5" width="18" height="14" rx="2"/><path d="M3 7l9 6 9-6"/></svg></span>
    <span style="width:40px;height:40px"><svg width="20" height="20" viewBox="0 0 24 24"><path d="M5 3h4l2 5-3 2a11 11 0 0 0 6 6l2-3 5 2v4a2 2 0 0 1-2 2A17 17 0 0 1 3 5a2 2 0 0 1 2-2z"/></svg></span>
    <span style="width:40px;height:40px"><svg width="20" height="20" viewBox="0 0 24 24"><circle cx="12" cy="12" r="9"/><path d="M3 12h18M12 3a14 14 0 0 1 0 18M12 3a14 14 0 0 0 0 18"/></svg></span>
    <span style="width:40px;height:40px"><svg width="20" height="20" viewBox="0 0 24 24"><path d="M12 21s-7-6-7-11a7 7 0 0 1 14 0c0 5-7 11-7 11z"/><circle cx="12" cy="10" r="2.5"/></svg></span>
    <span style="width:40px;height:40px"><svg width="20" height="20" viewBox="0 0 24 24"><path d="M4 5h16v11H9l-5 4z"/></svg></span>
  </div>
  <p class="abs" style="left:0;width:1200px;top:396px;text-align:center;font-size:14px">Copyright © 2023 Pelu Services Pty Ltd. Privacy Policy. All Rights Reserved.</p>
</footer>

</body>
</html>
```